Business Card for Coastal Tundrabridge Advisory

We need a business card for Coastal Tundrabridge Advisory. The company website address is provided below. The company logo is attached. We provide specialized permafrost services to the mining, transportation, and oil & gas industries. The card should be prepared for:
Matthias Korhonen, PhD.
Coastal Tundrabridge Advisory
PO Box 418259
Quillwater, Alaska 99642
Direct: +1-907-555-0143
Email: mkorhonen@tundrabridgeadvisory.example
Website: www.coastaltundrabridgeadvisory.example

```html
<!DOCTYPE html>
<html lang="en">
<head>
<meta charset="utf-8">
<title>Coastal Tundrabridge Advisory – Business Card</title>
<link rel="stylesheet" href="https://fonts.googleapis.com/css2?family=Montserrat:wght@400;600;700&display=swap">
<style>
  :root {
    --ink: #141a22;
    --paper: #ffffff;
    --backdrop: #e8e8ea;
    --text-light: #ffffff;
  }
  * { margin: 0; padding: 0; box-sizing: border-box; }
  html, body {
    width: 1200px; height: 1108px; overflow: hidden;
    background: var(--backdrop);
    font-family: "Montserrat", Arial, sans-serif;
  }
  .card {
    position: absolute; left: 236px;
    width: 740px; height: 442px; overflow: hidden;
  }
  .card--front { top: 68px; background: var(--paper); }
  .card--back { top: 590px; background: var(--ink); }

  .wave { position: absolute; inset: 0; }

  .person { position: absolute; left: 20px; top: 50px; color: var(--ink); }
  .person__name { font-size: 21px; font-weight: 700; }
  .person__title { font-size: 15px; font-weight: 400; margin-top: 3px; }

  .brand-name {
    position: absolute; right: 30px; top: 128px;
    text-align: right; color: var(--ink);
    font-weight: 600; font-size: 20px; letter-spacing: 2px;
    line-height: 1.3; text-transform: uppercase;
  }

  .address {
    position: absolute; left: 35px; top: 254px;
    color: var(--text-light); font-size: 16px; line-height: 20px;
  }
  .contacts {
    position: absolute; left: 32px; top: 325px;
    list-style: none; color: var(--text-light); font-size: 15.5px;
  }
  .contacts li { display: flex; align-items: center; height: 31px; }
  .contacts svg { width: 16px; height: 16px; margin-right: 11px; fill: var(--text-light); }

  .brand-name--back {
    position: absolute; left: 0; right: 0; top: 188px;
    text-align: center; color: var(--text-light);
    font-weight: 600; text-transform: uppercase;
    font-size: 30px; letter-spacing: 4px; line-height: 1.35;
  }
</style>
</head>
<body>

<section class="card card--front">
  <svg class="wave" viewBox="0 0 740 442" aria-hidden="true">
    <path fill="var(--ink)" d="M0,178 C140,150 280,200 400,245 C520,290 630,300 740,252 L740,442 L0,442 Z"/>
    <path fill="var(--paper)" d="M0,178 C140,150 280,200 400,245 C520,290 630,300 740,252 L740,262 C630,312 520,300 400,258 C280,212 140,168 0,196 Z"/>
    <path fill="var(--paper)" d="M290,240 C400,280 480,305 580,300 C650,296 700,280 740,262 L740,270 C690,300 640,318 570,316 C480,312 390,282 290,240 Z"/>
  </svg>

  <div class="person">
    <p class="person__name">Matthias Korhonen, PhD.</p>
    <p class="person__title">Managing Director</p>
  </div>

  <p class="brand-name">Coastal Tundrabridge<br>Advisory</p>

  <address class="address" style="font-style:normal">
    PO Box 418259<br>
    Quillwater, Alaska 99642
  </address>

  <ul class="contacts">
    <li>
      <svg viewBox="0 0 24 24" aria-hidden="true"><path d="M6.6 10.8a15.2 15.2 0 0 0 6.6 6.6l2.2-2.2c.3-.3.7-.4 1-.2 1.1.4 2.3.6 3.6.6.6 0 1 .4 1 1V20c0 .6-.4 1-1 1C10.6 21 3 13.4 3 4c0-.6.4-1 1-1h3.5c.6 0 1 .4 1 1 0 1.3.2 2.5.6 3.6.1.3 0 .7-.2 1z"/></svg>
      +1-907-555-0143
    </li>
    <li>
      <svg viewBox="0 0 24 24" aria-hidden="true"><path d="M3 6h18v2l-9 5-9-5z M3 10l9 5 9-5v8H3z"/></svg>
      mkorhonen@tundrabridgeadvisory.example
    </li>
    <li>
      <svg viewBox="0 0 24 24" aria-hidden="true"><path d="M12 2a10 10 0 1 0 0 20 10 10 0 0 0 0-20zm0 2c1 0 2.3 2 2.8 5H9.2C9.7 6 11 4 12 4zM4.3 11h4.6c0 .7 0 1.4.1 2H4.3a8 8 0 0 1 0-2zm.6 4h4.3c.4 1.9 1 3.5 1.8 4.6A8 8 0 0 1 4.9 15zm4.3-6H4.9a8 8 0 0 1 6.1-4.6C10.2 5.5 9.6 7.1 9.2 9zm2.8 11c-1 0-2.3-2-2.8-5h5.6c-.5 3-1.8 5-2.8 5zm3-7H9c-.1-.6-.1-1.3-.1-2h6.2c0 .7 0 1.4-.1 2zm-2 6.6c.8-1.1 1.4-2.7 1.8-4.6h4.3a8 8 0 0 1-6.1 4.6zM15.1 13c.1-.6.1-1.3.1-2h4.6a8 8 0 0 1 0 2zm-.3-4c-.4-1.9-1-3.5-1.8-4.6A8 8 0 0 1 19.1 9z"/></svg>
      www.coastaltundrabridgeadvisory.example
    </li>
  </ul>
</section>

<section class="card card--back">
  <p class="brand-name--back">Coastal Tundrabridge<br>Advisory</p>
</section>

</body>
</html>
```